RQV Wellness Co Business Card for food and Beverage Wizards & Alchemists

One main business card design for a wellness enterprise which represents two brands. We need one primary card design, for two different employees. The only difference between the cards will be the name, title and phone number for each employee, all other design elements will be same.
I've uploaded the logos for each brand. I have also uploaded a mockup which I made using Google's drawing tool. I can provide example images of business cards we find attractive if you would like some help picturing what we like.
I'm picturing the color splash on the back of the card below the two logos to be a dark burgundy or blue. This may sound a bit silly but the feel of the card and color should look almost like wizard dress robes. Dark emerald green, dark blue and dark burgundy with black undertones and gold lace.

Reason: Thank you all for the submissions. I will need some extra time to give you feedback. Cheers

Target Market(s)

Healthy food and beverage industry

Industry/Entity Type

Health And Wellness

Contact Information for Business Card

On one side we would like the business name, location, title of employee, employee name and contact details. On the flip side we would like our two brand logos and a splash of color. We would like the card to have a black font with some gold accents if possible. We would also like the trim of the business card or a middle ply within the card stock to have a color other than white.

Font styles to use
Serif

Colors
ec1f27
0255a3
00a990

Requirements
Must have
• Bold dark colors, happy to provide sample photos of business cards I like from snapgallery. Must have a version for two different employees. Must be sharp, modern and chic.
Nice to have
• Thick card stock layer in between the front and back of card that is either black or gold lace or something to make it feel, well let's say to make it feel expensive.
Should not have
• Should not have any cartoon-ey elements. All business.

```html
<!DOCTYPE html>
<html lang="en">
<head>
<meta charset="utf-8">
<title>RQV Wellness Co — Business Card</title>
<link href="https://fonts.googleapis.com/css2?family=Questrial&display=swap" rel="stylesheet">
<style>
  :root {
    --backdrop: #2b2b2d;
    --card: #232325;
    --gold: #a8661a;
    --ink-light: #f4f4f2;
  }
  * { margin: 0; padding: 0; box-sizing: border-box; }
  html, body {
    width: 1200px; height: 1017px; overflow: hidden;
    background: var(--backdrop);
    font-family: "Questrial", "Century Gothic", sans-serif;
  }
  .sheet {
    width: 1200px; height: 1017px;
    display: flex; align-items: center; justify-content: center; gap: 60px;
  }
  .card {
    width: 520px; height: 297px;
    background: var(--card);
    position: relative;
    box-shadow: 0 18px 40px rgba(0,0,0,.45);
  }
  .card--back {
    display: flex; align-items: center; justify-content: center; gap: 70px;
  }
  .brand-mark {
    display: flex; align-items: center; gap: 10px;
    color: var(--ink-light);
    font-size: 17px; letter-spacing: .06em;
  }
  .brand-mark__dot {
    width: 12px; height: 12px; border-radius: 50%;
    background: var(--ink-light);
  }
  .brand-mark__square {
    width: 12px; height: 12px;
    background: var(--ink-light);
  }
  .card--front {
    display: flex; flex-direction: column; align-items: center; justify-content: center;
    color: var(--gold); text-align: center;
  }
  .contact__name { font-size: 24px; font-weight: 700; letter-spacing: .04em; text-transform: uppercase; }
  .contact__title { font-size: 14px; margin-top: 2px; }
  .contact__rule { width: 44px; height: 1px; background: var(--gold); margin: 10px 0; opacity: .8; }
  .contact__line { font-size: 14px; line-height: 1.3; }
</style>
</head>
<body>
  <main class="sheet">
    <section class="card card--back" aria-label="Card back with brand names">
      <div class="brand-mark"><span class="brand-mark__dot"></span>Vale Tonics</div>
      <div class="brand-mark"><span class="brand-mark__square"></span>Prism Draught</div>
    </section>
    <section class="card card--front" aria-label="Card front with contact details">
      <h1 class="contact__name">Marcus Hale</h1>
      <p class="contact__title">Beverage Alchemist</p>
      <div class="contact__rule"></div>
      <p class="contact__line">RQV Wellness Co</p>
      <p class="contact__line">Oakridge, CA</p>
      <div class="contact__rule"></div>
      <p class="contact__line">415.555.0142</p>
      <p class="contact__line">rqvwellnessco@mailbox.com</p>
    </section>
  </main>
</body>
</html>
```